Business card design Needed for new logo / Construction business, home extensions and new builds

We need a business card design using our new logo files which i will attach to this project :)

We are a small construction business specialising in home extensions, new builds and property development. We are very ambitious and would appreciate professional and elegant designs for our new business card.

Very serious about using the services on MakerQuarry and recently acquired our new logo from here :)

Please get involved, i will feedback when i can as i am very busy but can respond daily, thanks

Target Market(s)

People that want to build onto their houses, new building developments or adding too their existing property

Industry/Entity Type

Construction

Contact Information for Business Card

Renwick Tolliver Construction, Lionel Ashby (Managing Director), Tel 07822254961, email - info@renwick-tolliver, www.renwick-tolliver.co.uk

Colors

Designer to choose colors to be used in the design.

Requirements
Must have
• I like a deep grey on the back please. A lot of you have provided black from and back, try mixing things up a little. The black looks cool 😎 Thanks

```html
<!DOCTYPE html>
<html lang="en">
<head>
<meta charset="utf-8">
<title>Renwick Tolliver Construction – Business Card</title>
<link rel="stylesheet" href="https://fonts.googleapis.com/css2?family=Montserrat:wght@400;600;700&display=swap">
<style>
  :root {
    --backdrop: #262628;
    --card-grey: #38383c;
    --gold: #e2a92c;
    --gold-light: #f7d46a;
    --silver: #c9cacc;
    --silver-dark: #9fa1a4;
    --text-light: #e8e8ea;
  }
  * { box-sizing: border-box; margin: 0; padding: 0; }
  html, body {
    width: 1200px; height: 689px; overflow: hidden;
    background: var(--backdrop);
    font-family: "Montserrat", sans-serif;
  }
  .card {
    position: absolute; top: 184px;
    width: 560px; height: 320px;
    background: var(--card-grey);
    border-radius: 18px;
    overflow: hidden;
  }
  .card--front { left: 26px; }
  .card--back { left: 614px; }

  /* Wordmark */
  .wordmark {
    position: absolute;
    display: flex; align-items: center; gap: 14px;
    color: var(--gold); font-weight: 600;
    text-transform: uppercase;
  }
  .wordmark__square {
    width: 34px; height: 34px; background: var(--gold); flex: none;
  }
  .wordmark__name { line-height: 1.25; letter-spacing: 0.08em; }
  .card--front .wordmark {
    left: 50%; top: 50%; transform: translate(-50%, -50%);
    font-size: 24px;
  }
  .card--front .wordmark__square { width: 44px; height: 44px; }
  .card--back .wordmark {
    left: 34px; top: 108px; font-size: 15px;
  }

  /* Back details */
  .divider {
    position: absolute; left: 268px; top: 52px;
    width: 1.5px; height: 176px; background: var(--gold);
  }
  .person { position: absolute; left: 290px; top: 56px; }
  .person__name { color: var(--gold); font-weight: 700; font-size: 22px; }
  .person__role { color: var(--text-light); font-size: 12.5px; margin-top: 2px; letter-spacing: 0.02em; }
  .contacts {
    position: absolute; left: 290px; top: 160px;
    list-style: none; color: var(--text-light); font-size: 12px;
  }
  .contacts li { display: flex; align-items: center; gap: 8px; margin-bottom: 7px; }
  .contacts svg { width: 12px; height: 12px; flex: none; fill: var(--gold); }
  .base-bands { position: absolute; left: 0; bottom: 0; width: 560px; height: 60px; }
</style>
</head>
<body>

<section class="card card--front" aria-label="Card front">
  <div class="wordmark">
    <span class="wordmark__square"></span>
    <span class="wordmark__name">Renwick Tolliver<br>Construction</span>
  </div>
</section>

<section class="card card--back" aria-label="Card back">
  <div class="wordmark">
    <span class="wordmark__square"></span>
    <span class="wordmark__name">Renwick Tolliver<br>Construction</span>
  </div>

  <div class="divider"></div>

  <div class="person">
    <p class="person__name">Lionel Ashby</p>
    <p class="person__role">Managing Director</p>
  </div>

  <ul class="contacts">
    <li>
      <svg viewBox="0 0 24 24"><path d="M6.6 10.8a15.1 15.1 0 0 0 6.6 6.6l2.2-2.2a1 1 0 0 1 1-.25 11.4 11.4 0 0 0 3.6.57 1 1 0 0 1 1 1V20a1 1 0 0 1-1 1A17 17 0 0 1 3 4a1 1 0 0 1 1-1h3.5a1 1 0 0 1 1 1c0 1.25.2 2.45.57 3.57a1 1 0 0 1-.25 1z"/></svg>
      07822254961
    </li>
    <li>
      <svg viewBox="0 0 24 24"><path d="M2 5h20v14H2z M2 5l10 8 10-8" fill="none" stroke="#e2a92c" stroke-width="2.2"/></svg>
      info@renwick-tolliver
    </li>
    <li>
      <svg viewBox="0 0 24 24"><circle cx="12" cy="12" r="9" fill="none" stroke="#e2a92c" stroke-width="2.2"/><path d="M3 12h18M12 3c3 3 3 15 0 18M12 3c-3 3-3 15 0 18" fill="none" stroke="#e2a92c" stroke-width="1.6"/></svg>
      www.renwick-tolliver.co.uk
    </li>
  </ul>

  <svg class="base-bands" viewBox="0 0 560 60" aria-hidden="true">
    <defs>
      <linearGradient id="silverBand" x1="0" x2="1">
        <stop offset="0" stop-color="#b9babd"/>
        <stop offset="0.5" stop-color="#e4e5e7"/>
        <stop offset="1" stop-color="#a9abae"/>
      </linearGradient>
      <linearGradient id="goldBand" x1="0" x2="1">
        <stop offset="0" stop-color="#d99a1f"/>
        <stop offset="0.45" stop-color="#f7d46a"/>
        <stop offset="1" stop-color="#e2a92c"/>
      </linearGradient>
    </defs>
    <polygon points="0,44 318,44 330,60 0,60" fill="url(#silverBand)"/>
    <polygon points="330,22 560,22 560,60 316,60 330,44" fill="url(#goldBand)"/>
  </svg>
</section>

</body>
</html>
```